Web Design Project - Shipping Industry

Goals and Objectives
The objective of the new website is to create a more modern look and feel. The site will also allow for a more effective means of communicating with members while providing the public with information and developments in the local, regional and international shipping industry.
Scope
The website will highlight the history of the organisation inclusive of text and photographs. It will take visitors through the years from beginning to present. Information on the history of the shipping industry will also be included.
It will feature current articles on the organisation, its members and stakeholders in the shipping industry. Member information as well as pertinent details regarding the organisation’s subsidiaries will be documented for the website.
Information as it relates to shipping statistics, case studies, laws and regulations, international treaties and trade documents, shipping terms, careers in shipping, job opportunities, training opportunities, information for shippers including port listing and trade lanes will be main features of the content for the website.
The Association’s community involvement, industry calendar events and related links relevant industry members will also be featured.
Target Market
• The General Public;
• Members of the organization;
• Shipping Industry Stakeholders (local, regional and international);
• Tertiary students conducting research.
• Potential employees
• Potential Business Partners
Best Practice Bench Marketing
The following websites are being looked at:
• Korvel Quayworks - http://www.korvelquayworks.example/ (preferred look)
• Tessaly Maritime Association - http://www.tma-freight.example/ (like image transition on main page)
• Drovna - http://www.drovna.example (professional look)
• PLW - http://www.pelworth.example (preferred color: blue in logo)
• Quillo - http://www.quillo.example/electronics/tv-video-audio/ (preferred look for links page: image + short text below + visit site link)
Expected Result
• 3 - 5 pages which must include: [1] main page [2] standard page [3] links page

```html
<!DOCTYPE html>
<html lang="en">
<head>
<meta charset="utf-8">
<title>Contact Us – Harbourline Shipping Association</title>
<link href="https://fonts.googleapis.com/css2?family=Arimo:ital,wght@0,400;0,700;1,400&family=Questrial&family=Tinos&display=swap" rel="stylesheet">
<style>
  :root {
    --bg-deep: #0a3fb8;
    --bg-light: #3f7be6;
    --brand: #1b49b5;
    --brand-dark: #0c3a9e;
    --link: #2a6bd6;
    --text: #222;
    --muted: #9aa3b2;
    --rule: #d6dbe3;
    --field: #c9d2de;
    --panel: #f1f2f4;
    --white: #fff;
  }
  * { box-sizing: border-box; margin: 0; padding: 0; }
  html, body { width: 1200px; height: 890px; overflow: hidden; }
  body {
    position: relative;
    font-family: "Arimo", sans-serif;
    color: var(--text);
    background: radial-gradient(ellipse at 50% 45%, var(--bg-light) 0%, var(--bg-deep) 70%);
  }
  .abs { position: absolute; }
  .page { position: absolute; left: 195px; top: 0; width: 805px; height: 837px; background: var(--white); }

  .brand { left: 240px; top: 12px; display: flex; align-items: center; gap: 12px; height: 44px; }
  .brand-dot { width: 46px; height: 40px; border-radius: 50%; background: var(--brand); }
  .brand-name { font-family: "Tinos", serif; font-size: 22px; color: var(--link); }

  .search { left: 782px; top: 34px; width: 168px; height: 19px; border: 1px solid var(--field); background: #f7f8fa; }
  .search span { position: absolute; left: 10px; top: 3px; font-size: 10px; font-style: italic; color: var(--muted); }
  .search-btn { position: absolute; right: -1px; top: -1px; width: 24px; height: 19px; background: var(--brand); }

  .nav { left: 240px; top: 75px; width: 715px; height: 22px; background: linear-gradient(#fafafa, #e9ebee); display: flex; font-family: "Questrial", sans-serif; font-size: 10px; }
  .nav a { text-decoration: none; color: #1d2f6a; display: flex; align-items: center; justify-content: center; border-right: 1px solid #c4c9d2; height: 12px; margin-top: 5px; }
  .nav a.current { background: var(--brand-dark); color: var(--white); height: 22px; margin-top: 0; border: 0; }

  .crumbs { left: 248px; top: 113px; font-size: 10px; display: flex; align-items: center; gap: 6px; }
  .crumbs a { color: var(--link); text-decoration: none; }
  .rule-top { left: 240px; top: 130px; width: 707px; border-top: 1px solid var(--rule); }

  .heading { left: 245px; top: 146px; font-family: "Questrial", sans-serif; font-size: 14px; color: var(--brand-dark); }
  .address, .contact-lines { top: 178px; font-size: 11px; line-height: 15.5px; }
  .address { left: 248px; }
  .address strong { color: var(--link); }
  .contact-lines { left: 512px; }
  .rule-dash { left: 247px; top: 249px; width: 493px; border-top: 1px dashed #b9c0cb; }

  .map { left: 243px; top: 277px; width: 234px; height: 231px; background: linear-gradient(135deg, #e4e1d9, #d5d2ca); border: 1px solid #cfd3d9; }
  .callout { left: 260px; top: 281px; width: 210px; height: 72px; background: var(--white); border-radius: 10px; box-shadow: 0 1px 4px rgba(0,0,0,.25); padding: 13px 0 0 17px; font-size: 9px; line-height: 11px; }
  .callout b { display: block; font-weight: 400; font-size: 11px; color: var(--link); margin-bottom: 4px; }
  .pin { left: 321px; top: 413px; }

  .routing { left: 243px; top: 529px; font-size: 11px; font-weight: 700; color: var(--link); }
  .postcode-label { left: 243px; top: 555px; font-size: 11px; }
  .field { position: absolute; border: 1px solid var(--field); border-radius: 3px; background: var(--white); }
  .btn { position: absolute; background: linear-gradient(#2f74e0, #0e46b6); color: var(--white); border-radius: 3px; font-size: 11px; display: flex; align-items: center; justify-content: center; }

  .label { position: absolute; left: 512px; font-size: 11px; }
  .select span { position: absolute; left: 10px; top: 6px; font-size: 11px; font-style: italic; color: var(--muted); }
  .captcha-code { left: 513px; top: 634px; font-size: 16px; font-weight: 700; color: var(--brand-dark); }

  .photo { left: 766px; top: 156px; width: 184px; height: 210px; background: linear-gradient(#9fbde6 0%, #b7c9df 50%, #6a5a48 80%, #8a8a86 100%); }
  .login { left: 765px; top: 381px; width: 186px; height: 54px; border: 1px solid #c6ccd6; }
  .login-art { position: absolute; left: 6px; top: 4px; width: 60px; height: 44px; background: linear-gradient(#dbe3ef, #4a5161); }
  .login span { position: absolute; left: 73px; top: 17px; font-family: "Questrial", sans-serif; font-size: 14px; color: var(--brand-dark); }
  .social { top: 464px; width: 36px; height: 24px; border-radius: 3px; }

  .partners { left: 238px; top: 739px; width: 711px; height: 74px; background: linear-gradient(90deg, #ebecee, #f8f8f9 50%, #ebecee); }
  .partners-title { left: 243px; top: 763px; font-family: "Questrial", sans-serif; font-size: 14px; line-height: 16px; color: var(--brand-dark); }
  .partner { top: 766px; font-size: 15px; font-weight: 700; color: var(--brand-dark); display: flex; align-items: center; gap: 6px; white-space: nowrap; }
  .partner i { width: 12px; height: 12px; background: var(--brand); display: inline-block; }

  .footer-note { left: 197px; top: 855px; font-size: 9px; color: var(--white); }
  .footer-brand { left: 694px; top: 848px; display: flex; align-items: center; gap: 8px; }
  .footer-brand .brand-dot { width: 36px; height: 30px; background: rgba(255,255,255,.85); }
  .footer-brand span { font-family: "Tinos", serif; font-size: 18px; color: var(--white); }
</style>
</head>
<body>
  <div class="page"></div>

  <header>
    <div class="abs brand"><span class="brand-dot"></span><span class="brand-name">Harbourline Shipping Association</span></div>
    <div class="abs search"><span>Search</span>
      <div class="search-btn"><svg width="24" height="19" viewBox="0 0 24 19"><circle cx="11" cy="8.5" r="3.5" fill="none" stroke="#fff" stroke-width="1.6"/><line x1="13.5" y1="11" x2="16" y2="13.5" stroke="#fff" stroke-width="1.8"/></svg></div>
    </div>
    <nav class="abs nav">
      <a style="width:72px">HOME</a><a style="width:85px">ABOUT US</a><a style="width:86px">PRODUCTS</a><a style="width:79px">SERVICES</a><a style="width:65px">NEWS</a><a style="width:77px">SUPPORT</a><a style="width:84px">PARTNERS</a><a style="width:87px">CUSTOMERS</a><a class="current" style="width:86px">CONTACT</a>
    </nav>
  </header>

  <div class="abs crumbs">
    <svg width="11" height="10" viewBox="0 0 11 10"><path d="M5.5 0 L11 5 H9 V10 H6.5 V7 H4.5 V10 H2 V5 H0 Z" fill="#2a6bd6"/></svg>
    <span>Home &gt; <a href="#">Contact Us</a></span>
  </div>
  <div class="abs rule-top"></div>

  <h1 class="abs heading">CONTACT US</h1>
  <div class="abs address"><strong>Harbourline Shipping Association</strong><br>12 Pier Road, Harbour View West,<br>P.O. Box 2040, Port Town 7, Jamaica W.I.</div>
  <div class="abs contact-lines">Tel: (555)410-2280-1, 410-2290-4<br>Fax:(555)410-2299<br>Email: info@harbourline.example</div>
  <div class="abs rule-dash"></div>

  <div class="abs map" role="img" aria-label="Street map showing the association office location"></div>
  <div class="abs callout"><b>Harbourline Shipping Association</b>12 Pier Road, Harbour View West,<br>P.O. Box 2040, Port Town 7<br>Jamaica W.I.</div>
  <svg class="abs pin" width="16" height="24" viewBox="0 0 16 24"><path d="M8 0 C3.5 0 0 3.5 0 8 C0 14 8 24 8 24 C8 24 16 14 16 8 C16 3.5 12.5 0 8 0 Z" fill="#e2493b" stroke="#8a1f15"/><circle cx="8" cy="8" r="2.5" fill="#7a1a12"/></svg>

  <div class="abs routing">Routing / driving directions:</div>
  <div class="abs postcode-label">Your postcode:</div>
  <div class="field" style="left:321px;top:549px;width:153px;height:28px"></div>
  <div class="btn" style="left:244px;top:592px;width:89px;height:27px">Get directions</div>

  <form>
    <div class="label" style="top:276px">Name</div>
    <div class="field" style="left:510px;top:293px;width:225px;height:26px"></div>
    <div class="label" style="top:329px">Phone</div>
    <div class="field" style="left:510px;top:346px;width:225px;height:26px"></div>
    <div class="label" style="top:382px">E-mail Address</div>
    <div class="field" style="left:510px;top:399px;width:225px;height:26px"></div>
    <div class="label" style="top:435px">Country</div>
    <div class="field select" style="left:510px;top:452px;width:225px;height:26px"><span>Jamaica - JM</span>
      <svg style="position:absolute;right:8px;top:10px" width="8" height="6" viewBox="0 0 8 6"><path d="M0 0 H8 L4 6 Z" fill="#333"/></svg></div>
    <div class="label" style="top:492px">Comment</div>
    <div class="field" style="left:508px;top:510px;width:226px;height:84px"></div>
    <div class="label" style="top:610px">Please enter the code you see in this box:</div>
    <div class="abs captcha-code">K2347</div>
    <div class="field" style="left:586px;top:632px;width:154px;height:28px"></div>
    <div class="btn" style="left:508px;top:678px;width:77px;height:26px">Send</div>
  </form>

  <aside>
    <div class="abs photo" role="img" aria-label="Photograph of a straddle carrier at a container port"></div>
    <div class="abs login"><div class="login-art" role="img" aria-label="Illustration of port staff reviewing documents"></div><span>MEMBER LOGIN</span></div>
    <div class="abs social" style="left:778px;background:#2f4f8f"></div>
    <div class="abs social" style="left:836px;background:#2a9fdc"></div>
    <div class="abs social" style="left:891px;background:#f2762b"></div>
  </aside>

  <section>
    <div class="abs partners"></div>
    <div class="abs partners-title">OUR<br>PARTNERS</div>
    <svg class="abs" style="left:330px;top:766px" width="14" height="22" viewBox="0 0 14 22"><path d="M11 2 L3 11 L11 20" fill="none" stroke="#b5b9c0" stroke-width="3"/></svg>
    <svg class="abs" style="left:923px;top:766px" width="14" height="22" viewBox="0 0 14 22"><path d="M3 2 L11 11 L3 20" fill="none" stroke="#b5b9c0" stroke-width="3"/></svg>
    <div class="abs partner" style="left:368px"><i></i>Norvane Lines</div>
    <div class="abs partner" style="left:508px"><i></i>Calder Docks</div>
    <div class="abs partner" style="left:651px"><i></i>Brightkeel</div>
    <div class="abs partner" style="left:790px"><i></i>Oriel Line</div>
  </section>

  <footer>
    <div class="abs footer-note">© Harbourline Shipping Association 2012, All Right Reserved</div>
    <div class="abs footer-brand"><span class="brand-dot"></span><span>Harbourline Shipping Association</span></div>
  </footer>
</body>
</html>
```